Harbor Ledger Funds Bus card and Logo

I need a logo design and Bus card design. The fund focuses on evaluating and investing in minerals (sub-surface rights) and real estate.

Harbor ledger refers to a book of knowledge that each plebe gets when entering the Kelmont Marine Academy (my alma mater)

Target Market(s)

Investors and financial advisors

Contact Information for Business Card

Simple - perhaps a logo with a theme on book of knowledge

Logo Text

Ex Scientia Imperium

Font styles to use
Serif
Sans Serif

Colors

Designer to choose colors to be used in the design.

Requirements
Must have
• memorable logo that is relatively simple

```html
<!DOCTYPE html>
<html lang="en">
<head>
<meta charset="utf-8">
<title>Harbor Ledger Funds – Business Card</title>
<link rel="stylesheet" href="https://fonts.googleapis.com/css2?family=Arimo:wght@400;700&display=swap">
<style>
  :root {
    --navy: #1f3466;
    --green: #9ccb3b;
    --white: #ffffff;
    --backdrop: #e9e9ec;
    --text-font: "Arimo", Arial, sans-serif;
  }
  * { margin: 0; padding: 0; box-sizing: border-box; }
  html, body {
    width: 1200px;
    height: 902px;
    overflow: hidden;
    background: var(--backdrop);
  }
  .canvas {
    position: relative;
    width: 1200px;
    height: 902px;
  }
  .business-card {
    position: absolute;
    left: 80px;
    top: 154px;
    width: 1040px;
    height: 594px;
    border-radius: 28px;
    overflow: hidden;
    background: var(--white);
    font-family: var(--text-font);
    box-shadow: 0 10px 30px rgba(0, 0, 0, 0.18);
  }
  .card-shapes {
    position: absolute;
    inset: 0;
  }
  .contact-side {
    position: absolute;
    left: 0;
    top: 0;
    width: 520px;
    height: 100%;
    color: var(--white);
  }
  .holder-name {
    position: absolute;
    left: 59px;
    top: 98px;
    font-size: 40px;
    font-weight: 700;
    line-height: 1;
  }
  .holder-title {
    position: absolute;
    left: 59px;
    top: 139px;
    font-size: 25px;
    line-height: 1;
  }
  .postal-address {
    position: absolute;
    left: 61px;
    top: 245px;
    font-size: 25px;
    line-height: 34px;
    font-style: normal;
  }
  .contact-list {
    position: absolute;
    left: 56px;
    top: 380px;
    list-style: none;
  }
  .contact-item {
    display: flex;
    align-items: center;
    height: 38px;
    font-size: 25px;
  }
  .contact-icon {
    width: 36px;
    height: 36px;
    margin-right: 12px;
    flex: none;
  }
  .web-accent { color: var(--green); }
  .brand-side {
    position: absolute;
    left: 560px;
    top: 0;
    width: 480px;
    height: 100%;
    display: flex;
    align-items: center;
    justify-content: center;
  }
  .brand-lockup {
    display: flex;
    align-items: center;
    gap: 18px;
  }
  .brand-dot {
    width: 48px;
    height: 48px;
    border-radius: 50%;
    background: var(--green);
    flex: none;
  }
  .brand-name {
    color: var(--navy);
    font-size: 38px;
    font-weight: 700;
    line-height: 1.1;
    letter-spacing: 1px;
    text-transform: uppercase;
  }
</style>
</head>
<body>
<main class="canvas">
  <article class="business-card">
    <svg class="card-shapes" viewBox="0 0 1040 594" width="1040" height="594" aria-hidden="true">
      <path class="navy-panel" d="M0 0 H540 Q400 297 540 594 H0 Z" fill="var(--navy)"/>
      <path class="green-arc" d="M548 0 Q420 297 548 594 Q436 297 548 0 Z" fill="var(--green)"/>
      <circle class="green-tab" cx="0" cy="130" r="34" fill="var(--green)"/>
    </svg>

    <section class="contact-side">
      <h1 class="holder-name">Dana Mercer</h1>
      <p class="holder-title">Manager</p>

      <address class="postal-address">
        PO BOX 418<br>
        Suite 7 Keel Row<br>
        2nd street Westport
      </address>

      <ul class="contact-list">
        <li class="contact-item">
          <svg class="contact-icon" viewBox="0 0 36 36" aria-hidden="true">
            <circle cx="18" cy="18" r="16" fill="var(--green)" stroke="var(--white)" stroke-width="1.5"/>
            <path d="M12 10 l4 0 l1.5 5 l-2.5 2 q2 4 5 5 l2 -2.5 l5 1.5 l0 4 q-10 1 -15 -15 z" fill="var(--navy)"/>
          </svg>
          <span>555.210.4873</span>
        </li>
        <li class="contact-item">
          <svg class="contact-icon" viewBox="0 0 36 36" aria-hidden="true">
            <circle cx="18" cy="18" r="16" fill="var(--green)" stroke="var(--white)" stroke-width="1.5"/>
            <rect x="9" y="12" width="18" height="12" fill="none" stroke="var(--navy)" stroke-width="2"/>
            <path d="M9 12 L18 19 L27 12" fill="none" stroke="var(--navy)" stroke-width="2"/>
          </svg>
          <span>info@harborledgerfunds.com</span>
        </li>
        <li class="contact-item">
          <svg class="contact-icon" viewBox="0 0 36 36" aria-hidden="true">
            <circle cx="18" cy="18" r="16" fill="var(--green)" stroke="var(--white)" stroke-width="1.5"/>
            <circle cx="18" cy="18" r="9" fill="none" stroke="var(--navy)" stroke-width="1.8"/>
            <ellipse cx="18" cy="18" rx="4" ry="9" fill="none" stroke="var(--navy)" stroke-width="1.5"/>
            <path d="M9 18 H27 M11 13 H25 M11 23 H25" stroke="var(--navy)" stroke-width="1.3"/>
          </svg>
          <span>www.<span class="web-accent">harborledger</span>.com</span>
        </li>
      </ul>
    </section>

    <section class="brand-side">
      <div class="brand-lockup">
        <span class="brand-dot" aria-hidden="true"></span>
        <p class="brand-name">Harbor Ledger<br>Funds LLC</p>
      </div>
    </section>
  </article>
</main>
</body>
</html>
```